Brightwell Aero Services Logo

I need a website and logo for the parent company Brightwell Aero Services, which encompasses general aviation aircraft repair, small aircrat rental and flight school. The company is based in Lawrenceville, Georgia at the Tolleson county airport. A saying that can be incorporated somehere could be, "Quality flying is safe flying", "Safety in mind is no accident" ,. I need a website and logo.

The company started as a repair shop performing repairs and inspections on Harlan, Vantor, Delkin and Ralstead general aviation aircraft, all models of single engine piston, multi engine piston, and single engine turboprop with an emphasis on Harlan Solvane and AeroTurn turbo prop aircraft. We have se=ince entered the aircraft rental and flight instruction market using the Delkin 240 ang Harlan Ranger aircraft.

Number of Pages; I don't know. Maybe 5 ? A home page for Brightwell Aero Services, page for maintenance and repairs and a couple for the rental and school. The maintenance shop is busy, always has been. I need to get the rental and school advertised and busy.

I have a logo for the maintenance shop shirts, not for the school. I do not have the file. I paid a business locally to do that and print on the shirts. They have the file.

Target Market(s)

In our flight school rental fleet department, we are looking for persons wishing to obtain their private pilot license and continuing on into their commercial and instrument ratings. In the aircraft maintenance department, we are looking for new customers who want a better and more quality relationship with their aircraft maintenance provider who will give more detail and quality in the repairs with an emphasis on safety and fewer problems between scheduled maintenance cycles on their aircraft. Brightwell's owner, Dale Hutchins, has been performing aircraft maintenance in the Atlanta area for 27 years. He has built a steady customer base through those years.

```html
<!DOCTYPE html>
<html lang="en">
<head>
<meta charset="utf-8">
<title>Brightwell Aero</title>
<link rel="stylesheet" href="https://fonts.googleapis.com/css2?family=Outfit:wght@500;600&family=Lato:wght@400;700&display=swap">
<style>
:root{
  --blue:#4f80e1;
  --navy:#0f1c47;
  --navy-card:#1b2d5e;
  --ink:#111;
  --text:#333;
  --field:#f7f7f8;
  --white:#fff;
}
*{box-sizing:border-box;margin:0;padding:0}
html,body{width:1200px;height:3551px;overflow:hidden;background:var(--white)}
body{position:relative;font-family:"Lato",sans-serif;color:var(--text)}
.abs{position:absolute}
h1,h2,h3,.brand{font-family:"Outfit",sans-serif;font-weight:600;color:var(--ink)}
.section-title{position:absolute;left:0;width:1200px;text-align:center;font-size:40px}

/* header */
.site-header{top:0;left:0;width:1200px;height:78px;background:var(--white)}
.brand{position:absolute;left:88px;top:14px;display:flex;align-items:center;gap:10px;font-size:32px}
.brand-mark{width:50px;height:50px;border-radius:50%;background:var(--blue);border:4px solid var(--navy)}
.main-nav{position:absolute;left:518px;top:27px;display:flex;gap:44px;font-size:15px}
.main-nav a{color:#222;text-decoration:none}
.header-phone{position:absolute;left:915px;top:17px;display:flex;align-items:center;gap:8px;font-family:"Outfit",sans-serif;font-weight:600;font-size:17px;color:var(--ink)}
.icon-circle{width:40px;height:40px;border-radius:50%;background:var(--blue);display:flex;align-items:center;justify-content:center}

/* hero */
.hero{top:78px;left:0;width:1200px;height:670px;background:linear-gradient(160deg,#5d646c 0%,#a9b0b8 35%,#d9dde2 60%,#8f969e 100%)}
.hero-swoosh{position:absolute;left:0;bottom:0}
.hero h1{position:absolute;left:111px;top:128px;color:var(--white);font-size:66px;line-height:76px}
.hero-sub{position:absolute;left:111px;top:296px;color:var(--white);font-size:21px}
.btn{display:flex;align-items:center;justify-content:center;background:var(--blue);color:var(--white);font-family:"Outfit",sans-serif;font-weight:600;text-decoration:none}
.hero .btn{position:absolute;left:112px;top:346px;width:174px;height:48px;border-radius:24px;font-size:15px}
.hero-dots{position:absolute;left:114px;top:481px;display:flex;gap:10px}
.hero-dots span{width:33px;height:3px;background:var(--white)}
.hero-dots span.on{background:var(--blue)}

/* services */
.card{position:absolute;border-radius:4px;overflow:visible}
.card-photo{position:absolute;inset:0;border-radius:4px}
.card h3{position:absolute;left:0;right:0;text-align:center;color:var(--white);font-size:25px;line-height:29px}
.card-toggle{position:absolute;width:42px;height:42px;border-radius:50%;background:var(--blue);display:flex;align-items:center;justify-content:center;left:50%;margin-left:-21px}
.card-feature{left:454px;top:916px;width:291px;height:387px;background:var(--navy-card)}
.card-feature p{position:absolute;left:22px;right:22px;top:156px;text-align:center;color:#e8ecf5;font-size:17px;line-height:28.5px}
.slider-dots{position:absolute;top:1360px;left:434px;display:flex;gap:15px}
.slider-dots span{width:58px;height:4px;background:#e1e3e8;border-radius:2px}
.slider-dots span.on{background:var(--blue)}

/* about */
.about{top:1500px;left:0;width:1200px;height:705px;background:linear-gradient(180deg,#fff 0%,#f4f5f7 25%,#dfe3e9 60%,#b9bec6 100%)}
.about h2{position:absolute;left:0;width:1200px;text-align:center;top:38px;font-size:36px}
.about p{position:absolute;left:170px;width:860px;top:100px;text-align:center;font-size:15.5px;line-height:25.8px;color:#222}
.about .btn{position:absolute;left:528px;top:280px;width:144px;height:53px;border-radius:4px;font-size:16px}

/* clients */
.clients-row{position:absolute;top:2360px;left:0;width:1200px;height:85px}
.client{position:absolute;top:0;height:82px;display:flex;align-items:center;justify-content:center;font-family:"Outfit",sans-serif;font-weight:600;font-size:34px;color:var(--ink)}
.client.active{background:var(--white);box-shadow:0 8px 30px rgba(0,0,0,.12)}
.arrow{position:absolute;top:30px}

/* contact */
.field{position:absolute;background:var(--field);font-size:15px;color:#444;padding:24px 19px}
.form .btn{position:absolute;left:487px;top:2928px;width:194px;height:53px;border-radius:27px;font-size:16px}

/* footer */
.footer-wave{position:absolute;left:0;top:3070px}
.footer{top:3200px;left:0;width:1200px;height:351px;color:var(--white)}
.footer h3{color:var(--white);font-size:22px;position:absolute;top:50px}
.footer .brand{left:106px;top:42px;font-size:28px;color:var(--white)}
.footer .brand-mark{width:40px;height:40px;border-width:3px;border-color:#fff}
.socials{position:absolute;left:162px;top:110px;display:flex;gap:9px}
.socials span{width:31px;height:31px;border-radius:50%;border:2px solid #fff;background:var(--blue)}
.footer ul{list-style:none;position:absolute;font-size:15px;line-height:30px}
.contact-list li{display:flex;gap:12px;align-items:flex-start;line-height:20px;margin-bottom:10px}
.newsletter-text{position:absolute;left:810px;top:88px;width:300px;font-size:15px;line-height:25px}
.newsletter{position:absolute;left:808px;top:153px;width:274px;height:42px;border-radius:21px;background:var(--white);color:#999;font-size:15px;padding:11px 20px}
.newsletter .icon-circle{position:absolute;right:3px;top:3px;width:36px;height:36px}
.footer-rule{position:absolute;left:108px;top:247px;width:984px;height:1px;background:rgba(255,255,255,.15)}
.copyright{position:absolute;left:0;width:1200px;top:292px;text-align:center;font-size:15px}
</style>
</head>
<body>

<header class="abs site-header">
  <div class="brand"><span class="brand-mark"></span>Brightwell Aero</div>
  <nav class="main-nav"><a href="#">Home</a><a href="#">About Us</a><a href="#">Services</a><a href="#">Contact</a></nav>
  <div class="header-phone">
    <span class="icon-circle"><svg width="18" height="18" viewBox="0 0 24 24"><path fill="#fff" d="M6.6 10.8a15.1 15.1 0 0 0 6.6 6.6l2.2-2.2c.3-.3.7-.4 1-.2 1.1.4 2.3.6 3.6.6.6 0 1 .4 1 1V20c0 .6-.4 1-1 1A17 17 0 0 1 3 4c0-.6.4-1 1-1h3.5c.6 0 1 .4 1 1 0 1.3.2 2.5.6 3.6.1.3 0 .7-.2 1z"/></svg></span>
    +1 888 888 8888
  </div>
</header>

<section class="abs hero" role="img" aria-label="Private jet flying above a sea of grey clouds">
  <h1>Quality Flying is<br>Safe Flying</h1>
  <p class="hero-sub">Safety in mind is no accident</p>
  <a class="btn" href="#">GET STARTED</a>
  <div class="hero-dots"><span></span><span class="on"></span><span></span><span></span></div>
  <svg class="hero-swoosh" width="1200" height="190" viewBox="0 0 1200 190">
    <path d="M0 175 C400 160 900 120 1200 0 L1200 190 L0 190Z" fill="#fff"/>
    <path d="M0 178 C500 175 950 135 1200 62 L1200 110 C950 160 500 188 0 188Z" fill="var(--blue)"/>
    <path d="M0 188 L1200 110 L1200 190 L0 190Z" fill="#fff"/>
  </svg>
</section>

<h2 class="section-title" style="top:828px">Our Services</h2>

<div class="card" style="left:179px;top:937px;width:258px;height:345px">
  <div class="card-photo" role="img" aria-label="Mechanic repairing an aircraft engine in a hangar" style="background:linear-gradient(160deg,#6b5448,#3b3b40 60%,#5a2f28)"></div>
  <h3 style="top:240px">Maintenance And<br>Repairs</h3>
  <span class="card-toggle" style="top:322px"><svg width="16" height="16" viewBox="0 0 16 16"><path d="M8 2v11M3 8l5 5 5-5" stroke="#fff" stroke-width="2" fill="none"/></svg></span>
</div>

<div class="card card-feature">
  <span class="card-toggle" style="top:40px"><svg width="16" height="16" viewBox="0 0 16 16"><path d="M8 14V3M3 8l5-5 5 5" stroke="#fff" stroke-width="2" fill="none"/></svg></span>
  <h3 style="top:110px">Small Aircraft Rental</h3>
  <p>Lorem ipsum dolor sit amet, consectetur adipiscing elit, sed do eiusmod tempor incididunt ut labore et dolore magna aliqua. Quis ipsum suspendisse ultrices gravida. Risus</p>
</div>

<div class="card" style="left:762px;top:937px;width:258px;height:345px">
  <div class="card-photo" role="img" aria-label="Flight instructor and student reviewing a checklist beside a small aircraft" style="background:linear-gradient(160deg,#8a8f96,#3e3a3a 55%,#5b6f8a)"></div>
  <h3 style="top:264px">Flight School</h3>
  <span class="card-toggle" style="top:322px"><svg width="16" height="16" viewBox="0 0 16 16"><path d="M8 2v11M3 8l5 5 5-5" stroke="#fff" stroke-width="2" fill="none"/></svg></span>
</div>

<div class="slider-dots"><span></span><span></span><span class="on"></span><span></span><span></span></div>

<section class="abs about" role="img" aria-label="Business jet parked on a runway in front of snowy mountains, faded">
  <h2>About Brightwell Aero</h2>
  <p>Lorem ipsum dolor sit amet, consectetur adipiscing elit, sed do eiusmod tempor incididunt ut labore et dolore magna aliqua. Quis ipsum suspendisse ultrices gravida. Risus commodo viverra maecenas accumsan lacus vel facilisis. Lorem ipsum dolor sit amet, consectetur adipiscing elit, sed do eiusmod tempor incididunt ut labore et dolore magna aliqua. Quis ipsum suspendisse ultrices gravida. Risus commodo viverra maecenas accumsan lacus vel facilisis. Lorem ipsum dolor sit amet, consectetur adipiscing elit, sed do eiusmod tempor incididunt ut labore et dolore magna aliqua. Quis ipsum suspendisse ultrices gravida. Risus commodo viverra maecenas accumsan lacus vel facilisis.</p>
  <a class="btn" href="#">Learn More</a>
</section>

<h2 class="section-title" style="top:2270px;font-size:38px">Our Clients</h2>
<div class="clients-row">
  <svg class="arrow" style="left:56px" width="14" height="20" viewBox="0 0 14 20"><path d="M10 3 3 10l7 7" stroke="#2c4fa0" stroke-width="2.5" fill="none"/></svg>
  <div class="client" style="left:160px;width:150px">Harlan</div>
  <div class="client active" style="left:370px;width:222px">Vantor</div>
  <div class="client" style="left:660px;width:150px">Delkin</div>
  <div class="client" style="left:870px;width:160px">Ralstead</div>
  <svg class="arrow" style="left:1130px" width="14" height="20" viewBox="0 0 14 20"><path d="M4 3l7 7-7 7" stroke="#bbb" stroke-width="2" fill="none"/></svg>
</div>

<h2 class="section-title" style="top:2558px;font-size:36px">Get In Touch With Us</h2>
<form class="form">
  <div class="field" style="left:189px;top:2658px;width:386px;height:52px;padding:16px 19px">First Name</div>
  <div class="field" style="left:590px;top:2658px;width:386px;height:52px;padding:16px 19px">Last Name</div>
  <div class="field" style="left:189px;top:2725px;width:386px;height:52px;padding:16px 19px">Email</div>
  <div class="field" style="left:590px;top:2725px;width:386px;height:52px;padding:16px 19px">Phone</div>
  <div class="field" style="left:189px;top:2793px;width:789px;height:105px;padding:18px 19px">Type Your Message Here</div>
  <a class="btn" href="#">Submit</a>
</form>

<svg class="footer-wave" width="1200" height="140" viewBox="0 0 1200 140">
  <path d="M0 75 C400 20 900 10 1200 15 L1200 140 L0 140Z" fill="var(--blue)"/>
  <path d="M0 115 C350 55 800 25 1200 20 L1200 140 L0 140Z" fill="var(--navy)"/>
  <path d="M0 120 L0 140 L30 140Z" fill="var(--navy)"/>
</svg>

<footer class="abs footer" style="background:var(--navy)">
  <div class="brand"><span class="brand-mark"></span>Brightwell Aero</div>
  <div class="socials"><span></span><span></span><span></span><span></span></div>

  <h3 style="left:418px">Quick Link</h3>
  <ul style="left:421px;top:92px"><li>Home</li><li>About Us</li><li>Services</li><li>Contact</li></ul>

  <h3 style="left:566px">Contact Us</h3>
  <ul class="contact-list" style="left:568px;top:98px">
    <li><svg width="14" height="18" viewBox="0 0 14 18"><path d="M7 0a7 7 0 0 0-7 7c0 5 7 11 7 11s7-6 7-11a7 7 0 0 0-7-7zm0 9.5A2.5 2.5 0 1 1 7 4.5a2.5 2.5 0 0 1 0 5z" fill="#fff"/></svg><span>12 b Brightwell Aero<br>Lorem ipsum dolor</span></li>
    <li><svg width="16" height="14" viewBox="0 0 16 14"><path d="M0 1h16v12H0z" fill="#fff"/><path d="M0 1l8 6 8-6" stroke="var(--navy)" stroke-width="1.5" fill="none"/></svg><span>info@brightwellaero.com</span></li>
    <li><svg width="14" height="14" viewBox="0 0 24 24"><path fill="#fff" d="M6.6 10.8a15.1 15.1 0 0 0 6.6 6.6l2.2-2.2c.3-.3.7-.4 1-.2 1.1.4 2.3.6 3.6.6.6 0 1 .4 1 1V20c0 .6-.4 1-1 1A17 17 0 0 1 3 4c0-.6.4-1 1-1h3.5c.6 0 1 .4 1 1 0 1.3.2 2.5.6 3.6.1.3 0 .7-.2 1z"/></svg><span>+1 888 888 8888</span></li>
  </ul>

  <h3 style="left:807px">Subscribe To Newsletter</h3>
  <p class="newsletter-text">Lorem ipsum dolor sit amet, consectetur adipiscing elit, sed do</p>
  <div class="newsletter">Enter Your Email
    <span class="icon-circle"><svg width="16" height="16" viewBox="0 0 16 16"><path d="M15 1 1 7l5 2 2 6z" fill="#fff"/></svg></span>
  </div>

  <div class="footer-rule"></div>
  <p class="copyright">©Copyrights 2023 &nbsp;Brightwell Aero &nbsp;| &nbsp;&nbsp;All Rights Reserved</p>
</footer>

</body>
</html>
```